furniture and home contents restoration

I need to list the services that we perform in our studio.
we serve the general public as well as the insurance/ remediation industry

```html
<!DOCTYPE html>
<html lang="en">
<head>
<meta charset="utf-8">
<title>Alder Hall Studio – Business Card</title>
<link rel="stylesheet" href="https://fonts.googleapis.com/css2?family=Montserrat:wght@800&family=Source+Sans+3:wght@400;600;700&display=swap">
<style>
  :root{
    --bg:#2c2e37;
    --navy:#1c2a33;
    --navy-gloss:#3d5564;
    --paper:#e1e2e7;
    --ink:#1c2a33;
    --ink-soft:#5e6670;
    --list:#c9d0d6;
    --list-head:#e6eaee;
    --rule:#8f959c;
  }
  *{box-sizing:border-box;margin:0;padding:0}
  html,body{width:1200px;height:1000px;overflow:hidden;background:var(--bg)}
  body{position:relative;font-family:"Source Sans 3",sans-serif}

  .card{position:absolute;width:560px;height:320px;border-radius:18px;overflow:hidden;box-shadow:0 14px 30px rgba(0,0,0,.35)}

  /* back side */
  .card-back{left:60px;top:150px;background:var(--navy);color:var(--list)}
  .card-back .brand{position:absolute;right:34px;top:34px;color:var(--navy-gloss);font-weight:700;font-size:26px;line-height:1;white-space:nowrap}
  .intro{position:absolute;left:34px;top:112px;font-size:13px;line-height:1.25}
  .intro strong{display:block;font-weight:700;color:var(--list-head)}
  .service-list{position:absolute;top:160px;list-style:none;font-size:12px;line-height:14.6px}
  .service-list.col-a{left:34px}
  .service-list.col-b{left:300px}
  .service-list li{display:flex;align-items:center;gap:7px;white-space:nowrap}
  .service-list svg{width:9px;height:9px;flex:none}

  /* front side */
  .card-front{left:580px;top:560px;background:var(--paper);color:var(--ink)}
  .card-front .brand{position:absolute;left:36px;top:96px;font-weight:700;font-size:30px;line-height:1;color:var(--ink);white-space:nowrap}
  .specialty{position:absolute;right:34px;top:26px;font-size:13px;color:var(--ink-soft)}
  .person{position:absolute;right:34px;top:98px;font-family:"Montserrat",sans-serif;font-weight:800;font-size:16px;letter-spacing:.3px}
  .person-rule{position:absolute;left:300px;right:34px;top:124px;height:1px;background:var(--rule)}
  .address{position:absolute;right:34px;top:138px;text-align:right;font-size:12.5px;line-height:1.3;color:var(--ink-soft)}
  .contact-rule{position:absolute;left:36px;width:150px;top:196px;height:1px;background:var(--rule)}
  .contacts{position:absolute;left:36px;top:204px;list-style:none;font-size:12.5px;line-height:15.5px;color:var(--ink-soft)}
  .contacts li{display:flex;align-items:center;gap:8px}
  .contacts svg{width:10px;height:10px;flex:none}
  .tagline{position:absolute;left:0;right:0;bottom:0;height:34px;background:var(--navy);color:#d6dbe0;font-size:13px;display:flex;align-items:center;justify-content:flex-end;padding-right:34px}
</style>
</head>
<body>

<svg width="0" height="0" style="position:absolute">
  <defs>
    <symbol id="tick" viewBox="0 0 10 10"><path d="M1.5 5.2 4 7.6 8.6 2.4" fill="none" stroke="currentColor" stroke-width="1.4" stroke-linecap="round" stroke-linejoin="round"/></symbol>
    <symbol id="phone" viewBox="0 0 10 10"><path d="M2.2 1 3.8 2.8 3 4.1c.6 1.3 1.6 2.3 2.9 2.9L7.2 6.2 9 7.8 8 9C4.5 8.8 1.2 5.5 1 2z" fill="currentColor"/></symbol>
    <symbol id="mobile" viewBox="0 0 10 10"><rect x="2.6" y=".6" width="4.8" height="8.8" rx="1" fill="none" stroke="currentColor" stroke-width="1"/><circle cx="5" cy="8" r=".5" fill="currentColor"/></symbol>
    <symbol id="fax" viewBox="0 0 10 10"><rect x="2.5" y=".8" width="5" height="3" fill="currentColor"/><rect x=".8" y="3.8" width="8.4" height="4" rx=".8" fill="currentColor"/><rect x="2.5" y="6.5" width="5" height="2.8" fill="#e1e2e7" stroke="currentColor" stroke-width=".8"/></symbol>
    <symbol id="mail" viewBox="0 0 10 10"><rect x=".6" y="2" width="8.8" height="6" fill="currentColor"/><path d="M.8 2.2 5 5.6 9.2 2.2" fill="none" stroke="#e1e2e7" stroke-width=".8"/></symbol>
  </defs>
</svg>

<section class="card card-back" aria-label="Card back: services">
  <div class="brand">Alder Hall Studio</div>
  <p class="intro"><strong>On-Site Inspections and Desk Review Services</strong>Assessment Reports and Estimates for Repair and Restoration</p>
  <ul class="service-list col-a">
    <li><svg><use href="#tick"/></svg>Antique Repair and Restoration</li>
    <li><svg><use href="#tick"/></svg>Art Cleaning and Remounting</li>
    <li><svg><use href="#tick"/></svg>Art and Mirror Frame Repair</li>
    <li><svg><use href="#tick"/></svg>Chandelier Cleaning and Restoration</li>
    <li><svg><use href="#tick"/></svg>Document Restoration</li>
    <li><svg><use href="#tick"/></svg>Glass, Ceramic and Mirror Repair</li>
    <li><svg><use href="#tick"/></svg>Hardware Repair and Restoration</li>
    <li><svg><use href="#tick"/></svg>Kitchen Removal and Reinstallation</li>
    <li><svg><use href="#tick"/></svg>Lamp Cleaning and Restoration</li>
    <li><svg><use href="#tick"/></svg>Lamp Shade Replacement</li>
  </ul>
  <ul class="service-list col-b">
    <li><svg><use href="#tick"/></svg>Metal Polishing and Restoration</li>
    <li><svg><use href="#tick"/></svg>Odor Removal and Ozone Services</li>
    <li><svg><use href="#tick"/></svg>Photo Restoration</li>
    <li><svg><use href="#tick"/></svg>Upholstery Cleaning and Deodorizing</li>
    <li><svg><use href="#tick"/></svg>In-House Upholstery and Reupholstery</li>
    <li><svg><use href="#tick"/></svg>Rug Cleaning and Restoration</li>
    <li><svg><use href="#tick"/></svg>Musical Instrument Restoration</li>
    <li><svg><use href="#tick"/></svg>Window Treatment Repair/ Restoration</li>
    <li><svg><use href="#tick"/></svg>Leather Restoration and Replacement</li>
    <li><svg><use href="#tick"/></svg>Piano Restoration and Repair</li>
  </ul>
</section>

<section class="card card-front" aria-label="Card front: contact">
  <div class="brand">Alder Hall Studio</div>
  <p class="specialty">Home Contents Restoration</p>
  <p class="person">DANIEL MARSH</p>
  <div class="person-rule"></div>
  <p class="address">82 Birchwood Hollow Rd.<br>Millbrook, NY 10599</p>
  <div class="contact-rule"></div>
  <ul class="contacts">
    <li><svg><use href="#phone"/></svg>555.310.2400</li>
    <li><svg><use href="#mobile"/></svg>555.684.1927</li>
    <li><svg><use href="#fax"/></svg>555.310.2460</li>
    <li><svg><use href="#mail"/></svg>desk@alderhallstudio.com</li>
  </ul>
  <div class="tagline">Serving The General Public and The Insurance Industry for Over 40 Years</div>
</section>

</body>
</html>
```